Brimvale display card for Lockout On Marlow

we need to design a display card for an lockout on marlow gift card that will be selling in brimvale. I' attached the specs and our logo, our website is lockoutonmarlow.com.

the offer will be 2x $50.00 gift cards for $79.99.

i also prefer our logo with the black background.

```html
<!DOCTYPE html>
<html lang="en">
<head>
<meta charset="utf-8">
<title>Lockout On Marlow – Brimvale Display Card</title>
<link href="https://fonts.googleapis.com/css2?family=Anton&family=Roboto+Condensed:wght@700&display=swap" rel="stylesheet">
<style>
  :root {
    --stage: #3b3b3d;
    --card-deep: #0e1318;
    --card-blue: #1f4a60;
    --card-teal: #2b6580;
    --frame-blue: #3d6a80;
    --header-grey: #5e6063;
    --ink-white: #ffffff;
    --fpo-pink: #e6157d;
    --title-gold: #f6df7a;
    --title-red: #a52a1c;
    --title-orange: #f04e14;
  }
  * { box-sizing: border-box; margin: 0; padding: 0; }
  html, body { width: 1200px; height: 900px; overflow: hidden; }
  body { background: var(--stage); position: relative; font-family: "Roboto Condensed", Arial, sans-serif; }

  .display-card {
    position: absolute; top: 124px; width: 505px; height: 650px;
    border-radius: 44px 44px 34px 34px; overflow: hidden;
  }
  .display-card--front { left: 85px; background: linear-gradient(180deg, var(--card-teal) 0%, var(--card-blue) 30%, var(--card-deep) 80%); }
  .display-card--back { left: 612px; background: var(--frame-blue); padding: 15px; }

  .hang-slot {
    position: absolute; top: 12px; left: 50%; transform: translateX(-50%);
    width: 66px; height: 26px; border-radius: 6px; background: #1a1a1a; z-index: 3;
  }
  .hang-slot::after {
    content: ""; position: absolute; left: 50%; top: 5px; transform: translateX(-50%);
    width: 14px; height: 12px; border-radius: 7px 7px 2px 2px; background: var(--stage);
  }

  .card-header {
    position: absolute; top: 0; left: 0; right: 0; height: 60px;
    background: linear-gradient(180deg, var(--header-grey), #2f3032);
    border-bottom: 3px solid var(--ink-white);
  }
  .card-footer {
    position: absolute; bottom: 0; left: 0; right: 0; height: 38px;
    background: #111; border-top: 3px solid var(--ink-white);
  }
  .notice {
    position: absolute; width: 180px; color: var(--ink-white);
    font-size: 8px; line-height: 1.2; text-transform: uppercase;
  }
  .card-header .notice { top: 20px; }
  .card-footer .notice { top: 6px; }
  .notice--en { left: 26px; }
  .notice--fr { left: 290px; }

  .offer { position: absolute; top: 88px; right: 22px; text-align: right; color: var(--ink-white); font-family: "Anton", Impact, sans-serif; }
  .offer__qty { font-size: 44px; line-height: 1; }
  .offer__price { font-size: 21px; line-height: 1.1; }

  .brand-mark {
    position: absolute; top: 288px; left: 205px; width: 72px; height: 72px;
    border-radius: 50%; background: var(--card-teal);
  }
  .brand-name {
    position: absolute; top: 196px; left: 100px;
    font-family: "Anton", Impact, sans-serif; color: var(--ink-white);
    font-size: 82px; line-height: 0.98;
  }
  .gift-card-label {
    position: absolute; top: 516px; left: 0; right: 0; text-align: center;
    font-family: "Anton", Impact, sans-serif; color: var(--ink-white);
    font-size: 40px; letter-spacing: 22px; padding-left: 22px;
  }

  .item-tag { position: absolute; text-align: center; color: var(--ink-white); font-size: 7px; }
  .item-tag__fpo {
    display: block; margin-top: 3px; padding: 2px 5px; background: var(--fpo-pink);
    border: 2px solid var(--ink-white); font-family: "Anton", Impact, sans-serif; font-size: 15px; letter-spacing: 1px;
  }
  .display-card--front .item-tag { right: 40px; top: 570px; }
  .display-card--back .item-tag { right: 54px; top: 574px; }

  .back-panel {
    position: relative; width: 100%; height: 100%; border-radius: 30px; overflow: hidden;
    background: linear-gradient(160deg, var(--card-blue), var(--card-deep) 75%);
  }
  .room-photo { position: absolute; left: 0; width: 262px; height: 204px; border-bottom: 2px solid var(--frame-blue); }
  .room-photo--chains { top: 0; background: linear-gradient(135deg, #3a2a1e, #1d1511); }
  .room-photo--fire { top: 204px; background: radial-gradient(circle at 60% 45%, #d64030, #5a0d0a 70%); }
  .room-photo--cabin { top: 408px; height: 212px; background: linear-gradient(180deg, #2b2d30, #6f7580); }

  .room-title {
    position: absolute; right: 50px; text-align: right;
    font-family: "Anton", Impact, sans-serif; font-size: 38px; line-height: 1.12;
  }
  .room-title--showdown { top: 70px; color: var(--title-gold); }
  .room-title--smoke { top: 262px; color: var(--title-red); }
  .room-title--crater { top: 470px; color: var(--title-orange); }
</style>
</head>
<body>

<section class="display-card display-card--front" aria-label="Lockout On Marlow gift card display, front">
  <div class="hang-slot"></div>
  <header class="card-header">
    <p class="notice notice--en">To purchase this item, please take this card to the cash register and exchange for the quantity you wish to purchase.</p>
    <p class="notice notice--fr">Veuillez présenter cette carte à la caisse pour l'échanger contre le nombre d'articles que vous souhaitez acheter.</p>
  </header>

  <div class="offer">
    <p class="offer__qty">2x$50</p>
    <p class="offer__price">for $79.99</p>
  </div>

  <div class="brand-mark"></div>
  <h1 class="brand-name">LOCKOUT<br>ON<br>MARLOW</h1>

  <p class="gift-card-label">GIFT CARD</p>

  <div class="item-tag">ITM./ART.<span class="item-tag__fpo">F.P.O.</span></div>

  <footer class="card-footer">
    <p class="notice notice--en">Do not remove this card from the warehouse. This card has no monetary value.</p>
    <p class="notice notice--fr">Ne pas sortir cette carte de l'entrepôt. Cette carte n'a aucune valeur marchande.</p>
  </footer>
</section>

<section class="display-card display-card--back" aria-label="Lockout On Marlow gift card display, back">
  <div class="hang-slot"></div>
  <div class="back-panel">
    <div class="room-photo room-photo--chains" role="img" aria-label="Close-up of chained hands in a dim room"></div>
    <div class="room-photo room-photo--fire" role="img" aria-label="Arm holding a flashlight through red smoke"></div>
    <div class="room-photo room-photo--cabin" role="img" aria-label="Interior of an aircraft cabin with rows of seats"></div>

    <h2 class="room-title room-title--showdown">GHOST TOWN<br>SHOWDOWN</h2>
    <h2 class="room-title room-title--smoke">SMOKE ALARM<br>RESCUE</h2>
    <h2 class="room-title room-title--crater">CRATER SKIES:<br>FLIGHT DECK</h2>

    <div class="item-tag">ITM./ART.<span class="item-tag__fpo">F.P.O.</span></div>
  </div>
</section>

</body>
</html>
```